Upscale business cards needed for Board of Directors

We need professional business cards created for members of our family business Board of Directors. We would like these relatively simple and straightforward, but also with a unique element to set them apart. Probably stick with neutral and simple colors - white, grey etc. We need space for the traditional elements, including name, title, address, email/phone number. And we will be creating several from this template so it needs to be template that is easy to switch information in and out of.
Business
See description

```html
<!DOCTYPE html>
<html lang="en">
<head>
<meta charset="utf-8">
<title>Harborline Holdings — Business Cards</title>
<link href="https://fonts.googleapis.com/css2?family=Lato:wght@400;700;900&display=swap" rel="stylesheet">
<style>
  :root {
    --stage: #e4e4e2;
    --gold: #b09d72;
    --ink: #111111;
    --paper: #ffffff;
    --muted-gold: #a8956a;
    --divider: #555555;
  }
  html, body {
    margin: 0;
    padding: 0;
    width: 1200px;
    height: 900px;
    overflow: hidden;
    background: var(--stage);
    font-family: "Lato", sans-serif;
  }
  .canvas {
    position: relative;
    width: 1200px;
    height: 900px;
  }
  .card {
    position: absolute;
    width: 560px;
    height: 320px;
    box-shadow: 0 10px 28px rgba(0,0,0,0.18);
    box-sizing: border-box;
  }
  /* Back of card */
  .card-back {
    left: 560px;
    top: 90px;
    background: var(--gold);
    display: flex;
    flex-direction: column;
    align-items: center;
    justify-content: center;
  }
  .brand-name {
    font-family: "Lato", sans-serif;
    font-weight: 900;
    color: var(--ink);
    text-transform: uppercase;
    text-align: center;
    line-height: 1.05;
    margin: 0;
  }
  .card-back .brand-name {
    font-size: 44px;
    letter-spacing: 1px;
  }
  .card-back .brand-name span {
    display: block;
    font-size: 24px;
    letter-spacing: 9px;
  }
  .card-back .website {
    margin-top: 46px;
    color: var(--paper);
    font-size: 15px;
    letter-spacing: 2px;
  }
  /* Front of card */
  .card-front {
    left: 80px;
    top: 480px;
    background: var(--paper);
    display: flex;
    align-items: center;
  }
  .front-brand {
    width: 270px;
    display: flex;
    justify-content: center;
  }
  .card-front .brand-name {
    font-size: 30px;
  }
  .card-front .brand-name span {
    display: block;
    font-size: 17px;
    letter-spacing: 6px;
  }
  .front-divider {
    width: 1px;
    height: 220px;
    background: linear-gradient(to bottom, transparent, var(--divider) 40%, var(--divider) 60%, transparent);
  }
  .contact {
    padding-left: 34px;
    color: var(--ink);
  }
  .person-name {
    font-size: 24px;
    margin: 0;
    font-weight: 400;
  }
  .person-title {
    font-size: 15px;
    color: var(--muted-gold);
    margin: 0 0 10px;
  }
  .address {
    font-size: 15px;
    line-height: 1.3;
    margin: 0 0 8px;
  }
  .contact-list {
    list-style: none;
    margin: 0;
    padding: 0;
    font-size: 15px;
  }
  .contact-list li {
    display: flex;
    align-items: center;
    gap: 10px;
    line-height: 1.45;
  }
  .contact-list svg {
    width: 13px;
    height: 13px;
    fill: var(--muted-gold);
    flex: none;
  }
</style>
</head>
<body>
<div class="canvas">

  <section class="card card-back" aria-label="Card back">
    <p class="brand-name">Harborline<span>Holdings</span></p>
    <div class="website">www.harborline.com</div>
  </section>

  <section class="card card-front" aria-label="Card front">
    <div class="front-brand">
      <p class="brand-name">Harborline<span>Holdings</span></p>
    </div>
    <div class="front-divider"></div>
    <div class="contact">
      <h1 class="person-name">Mark Ellison</h1>
      <p class="person-title">Director</p>
      <p class="address">1450 Cedar Row<br>Marlow TX 78010</p>
      <ul class="contact-list">
        <li>
          <svg viewBox="0 0 16 16" aria-hidden="true"><path d="M3 1l3 3-1.5 2c1 2 3 4 5.5 5.5L12 10l3 3-2 2C7 15 1 9 1 3z"/></svg>
          512 555 0140
        </li>
        <li>
          <svg viewBox="0 0 16 16" aria-hidden="true"><rect x="4" y="1" width="8" height="4"/><rect x="1" y="6" width="14" height="6" rx="1"/><rect x="4" y="10" width="8" height="5"/></svg>
          512 555 0141
        </li>
        <li>
          <svg viewBox="0 0 16 16" aria-hidden="true"><path d="M1 3h14v10H1z M1 3l7 6 7-6" fill="none" stroke="#a8956a" stroke-width="1.6"/></svg>
          info@harborline.com
        </li>
        <li>
          <svg viewBox="0 0 16 16" aria-hidden="true"><circle cx="8" cy="8" r="6.5" fill="none" stroke="#a8956a" stroke-width="1.4"/><path d="M1.5 8h13M8 1.5c-3 3.5-3 9.5 0 13M8 1.5c3 3.5 3 9.5 0 13" fill="none" stroke="#a8956a" stroke-width="1.2"/></svg>
          www.harborline.com
        </li>
      </ul>
    </div>
  </section>

</div>
</body>
</html>
```